Zolvana Stationary and Branding Documents

Corporate Identity Branding stationary needed for IT Recruiting Firm.

I already have a Logo, business cards and website. I need to get designs completed for the remaining corporate identity documents.

The documentation should use similar colors as my website and business card. The designs should modern and clean.

http://zolvanaworks.example/

Target Market(s)

Information Technology Industry

Industry/Entity Type

Information Technology

Colors
3377b5
0255a3
fbee3e
f78f20
f37122
33a6d7
000000
0592cd

Requirements
Must have
• Letter Head
• Folder Design
• PowerPoint Design
• Invoice
• Envelope
Nice to have
• Proposal
• Flyer
• Brochure
Should not have
• Logo
• Business Cards
• Website

```html
<!DOCTYPE html>
<html lang="en">
<head>
<meta charset="utf-8">
<title>Zolvana Letterhead</title>
<link href="https://fonts.googleapis.com/css2?family=Open+Sans:wght@400;600&display=swap" rel="stylesheet">
<style>
  :root {
    --bg: #e9edf6;
    --paper: #f7f8f9;
    --blue: #1b5e9e;
    --orange: #e0782e;
    --orange-dark: #c9591c;
    --accent-soft-a: #f8efe4;
    --accent-soft-b: #efe7df;
    --ink: #5a6068;
  }
  * { margin: 0; padding: 0; box-sizing: border-box; }
  html, body { width: 1200px; height: 784px; overflow: hidden; }
  body {
    background: var(--bg);
    font-family: "Open Sans", Arial, sans-serif;
    position: relative;
  }
  .letterhead {
    position: absolute;
    left: 360px;
    top: 52px;
    width: 480px;
    height: 680px;
    background: var(--paper);
    box-shadow: 0 6px 24px rgba(40, 60, 120, 0.18);
    overflow: hidden;
  }
  .top-rule {
    position: absolute;
    left: 0; right: 0; top: 0;
    height: 3px;
    background: var(--blue);
  }
  .brand {
    position: absolute;
    left: 30px;
    top: 26px;
    display: flex;
    align-items: center;
    gap: 8px;
  }
  .brand-mark { width: 10px; height: 10px; background: var(--orange); }
  .brand-name {
    font-size: 30px;
    font-weight: 600;
    color: var(--blue);
    letter-spacing: 0.5px;
    line-height: 1;
  }
  .contact {
    position: absolute;
    right: 26px;
    top: 34px;
    list-style: none;
    font-size: 6.5px;
    line-height: 10px;
    color: var(--ink);
  }
  .contact li { display: flex; align-items: flex-start; gap: 5px; }
  .contact .icon {
    flex: none;
    width: 6px;
    height: 6px;
    margin-top: 2px;
    border-radius: 50%;
    background: var(--blue);
  }
  .watermark-area {
    position: absolute;
    left: 36px;
    right: 36px;
    top: 430px;
    height: 110px;
    background: linear-gradient(90deg, var(--accent-soft-a), var(--accent-soft-b));
    opacity: 0.6;
  }
  .footer-band {
    position: absolute;
    left: 0; right: 0; bottom: 0;
    height: 40px;
    background: linear-gradient(90deg, var(--orange-dark), var(--orange));
  }
  .footer-rule {
    position: absolute;
    left: 0; right: 0; bottom: 40px;
    height: 4px;
    background: var(--blue);
  }
</style>
</head>
<body>
  <main class="letterhead">
    <div class="top-rule"></div>

    <header class="brand">
      <span class="brand-mark"></span>
      <span class="brand-name">Zolvana</span>
    </header>

    <ul class="contact">
      <li><span class="icon"></span><span>Two Harbor Plaza 410<br>Ninth Street NW</span></li>
      <li><span class="icon"></span><span>555 010 4821</span></li>
      <li><span class="icon"></span><span>info@zolvanaworks.example</span></li>
      <li><span class="icon"></span><span>www.zolvanaworks.example</span></li>
    </ul>

    <div class="watermark-area" role="img" aria-label="Faint decorative background motif in pale peach tones"></div>

    <div class="footer-rule"></div>
    <div class="footer-band"></div>
  </main>
</body>
</html>
```